Flyer Design Project

I require a double sided flyer in PSD format.
The flyer should look fresh and clean.
The flyer is for an digital marketing company that offers various services. The services are broken down into 3 main categories and the design should reflect this.
All the content is provided in the attached file
Industry/Entity Type
Digital
Requirements
Must have
- Front of the leaflet to be mainly white background with appealing text based questions in the colours in large font with relevant images.
Back if the
3 separate boxes using the colours indicated in the attachment for the services on back of the leafet.
Should not have
- Gradients
Borders on the edges of the design
Vignettes
Black elements
Any text below 10pt
Fancy fonts
Do not use old-style fonts

```html
<!DOCTYPE html>
<html lang="en">
<head>
<meta charset="utf-8">
<title>Digital Marketing Flyer – Front and Back</title>
<link href="https://fonts.googleapis.com/css2?family=Quicksand:wght@400;500;600;700&display=swap" rel="stylesheet">
<style>
  :root{
    --green:#8dc63f;
    --green-dark:#119a48;
    --blue:#3cbfe3;
    --blue-dark:#1f6db7;
    --orange:#f47f20;
    --orange-dark:#e2692a;
    --white:#ffffff;
    --stage:#ece9e4;
  }
  *{box-sizing:border-box;margin:0;padding:0}
  html,body{width:1200px;height:1000px;overflow:hidden}
  body{background:var(--stage);font-family:"Quicksand",sans-serif;position:relative}

  .flyer{position:absolute;top:60px;width:560px;height:860px;background:var(--white);overflow:hidden}
  .flyer--back{left:25px}
  .flyer--front{left:615px}

  /* back side */
  .bands{position:absolute;inset:0}
  .service{position:absolute;left:0;width:500px;color:var(--white)}
  .service ul{list-style:none;padding-left:42px}
  .service li{font-size:23px;font-weight:500;line-height:29px;position:relative}
  .service li::before{content:"•";position:absolute;left:-18px}
  .service b{font-weight:700}
  .service--consulting{top:22px}
  .service--design{top:214px}
  .service--sem{top:420px}

  .offer{margin:18px 0 0 42px;width:410px;border:2px dashed var(--white);padding:6px 0;text-align:center;font-weight:700;font-size:24px;line-height:26px;color:var(--white)}
  .offer .free{color:var(--orange)}
  .offer--consulting{background:var(--green-dark)}
  .offer--design{background:var(--blue-dark);margin-top:14px}
  .offer--sem{background:var(--orange-dark);margin-top:16px;font-size:22px}
  .offer--sem small{display:block;font-size:19px}

  .category{position:absolute;right:6px;writing-mode:vertical-rl;color:var(--orange);font-size:16px;line-height:19px;letter-spacing:.5px}
  .category b{font-weight:700}
  .category--consulting{top:32px}
  .category--design{top:262px}
  .category--sem{top:520px}

  .back-footer{position:absolute;left:42px;top:775px;color:var(--orange);font-size:15px;font-weight:600;line-height:20px}
  .back-footer svg{vertical-align:-2px;margin-right:3px}
  .back-footer strong{font-weight:700;font-size:17px}
  .logo-box{position:absolute;background:var(--blue);color:var(--white);text-align:center;font-weight:700;line-height:1}
  .logo-box--small{left:445px;top:776px;width:100px;height:36px;font-size:13px;padding-top:4px}

  /* front side */
  .pitch{position:absolute;text-transform:uppercase;line-height:1}
  .pitch--stat{left:40px;top:24px}
  .stat-intro{color:var(--green);font-size:26px;font-weight:500}
  .stat-figure{color:var(--orange);font-size:104px;font-weight:700;letter-spacing:-2px;display:inline-block;margin-top:-4px}
  .stat-figure span{font-size:26px;letter-spacing:0}
  .stat-arrow{position:absolute;left:178px;top:58px}
  .stat-text{color:var(--green);font-size:28px;font-weight:500;line-height:32px;margin-top:2px}
  .stat-text b,.pitch--finding b{color:var(--orange);font-weight:700}

  .rule{position:absolute;left:0;height:2px;background:var(--orange)}
  .rule::before{content:"";position:absolute;left:0;top:-2px;width:70px;height:6px;background:var(--orange)}
  .rule--one{top:246px;width:540px}
  .rule--two{top:372px;width:520px}
  .rule--three{top:628px;width:500px}

  .pitch--finding{left:40px;top:274px;color:var(--green);font-size:32px;font-weight:500;line-height:36px}
  .pitch--more{left:40px;top:394px;color:var(--green)}
  .more-intro{font-size:32px;letter-spacing:10px;font-weight:500}
  .more-word{font-size:118px;font-weight:700;letter-spacing:-2px;line-height:100px}
  .more-customers{color:var(--orange);font-size:52px;font-weight:500;line-height:50px}
  .more-business{font-size:32px;font-weight:500;line-height:36px}
  .tagline{position:absolute;left:40px;top:642px;color:var(--orange);font-size:17px;font-weight:700}

  .front-wave{position:absolute;left:0;bottom:0}
  .logo-box--large{left:300px;top:692px;width:220px;height:100px;font-size:36px;padding-top:16px}
  .logo-box--large span{font-weight:500;display:block}
  .front-call{position:absolute;left:20px;top:806px;color:var(--white);font-size:17px;font-weight:500}
  .front-call strong{font-weight:700}
</style>
</head>
<body>

<section class="flyer flyer--back" aria-label="Flyer back: services">
  <svg class="bands" width="560" height="860" viewBox="0 0 560 860" aria-hidden="true">
    <path d="M0 0 H500 Q445 100 545 200 L0 200 Z" fill="var(--green)"/>
    <path d="M0 200 H545 Q445 305 545 410 L0 410 Z" fill="var(--blue)"/>
    <path d="M0 410 H545 Q430 575 545 740 L0 740 Z" fill="var(--orange)"/>
  </svg>

  <div class="service service--consulting">
    <ul>
      <li>Marketing <b>strategy</b> and <b>planning</b></li>
      <li>Business <b>branding</b></li>
      <li>Competition <b>analysis</b>,</li>
    </ul>
    <div class="offer offer--consulting">GET<br><span class="free">FREE</span> CONSULTATION</div>
  </div>
  <div class="category category--consulting"><b>CONSULTING</b><br>SERVICES</div>

  <div class="service service--design">
    <ul>
      <li>Web Design</li>
      <li>Website maintenance</li>
      <li>Logo design</li>
      <li>Flyer design</li>
    </ul>
    <div class="offer offer--design">GET<br><span class="free">FREE</span> WEBSITE</div>
  </div>
  <div class="category category--design"><b>DESIGN</b><br>SERVICES</div>

  <div class="service service--sem">
    <ul>
      <li>Local Business Marketing</li>
      <li>PPC</li>
      <li>Email marketing</li>
      <li>SEO</li>
      <li>Social media</li>
      <li>Content development</li>
      <li>Website audit</li>
      <li>Lead generation</li>
    </ul>
    <div class="offer offer--sem">25% OFF<small>any SEM Package</small></div>
  </div>
  <div class="category category--sem"><b>SEM</b><br>SERVICES</div>

  <div class="back-footer">
    <svg width="11" height="15" viewBox="0 0 11 15" aria-hidden="true"><path d="M5.5 0A5.5 5.5 0 0 0 0 5.5C0 9.5 5.5 15 5.5 15S11 9.5 11 5.5A5.5 5.5 0 0 0 5.5 0Zm0 7.7a2.2 2.2 0 1 1 0-4.4 2.2 2.2 0 0 1 0 4.4Z" fill="var(--orange)"/></svg>Lumen, 12 Canal Walk, Harbourton, HB4 7QX<br>
    Call <strong>0100 555 0192</strong> for a <strong>FREE</strong>
  </div>
  <div class="logo-box logo-box--small">LOGO<br>HERE</div>
</section>

<section class="flyer flyer--front" aria-label="Flyer front: questions">
  <div class="pitch pitch--stat">
    <div class="stat-intro">Did you know</div>
    <div class="stat-figure">85<span>%</span></div>
    <div class="stat-text">of consumers use the internet<br>to find <b>business</b> like yours ?</div>
  </div>
  <svg class="stat-arrow" width="40" height="90" viewBox="0 0 40 90" aria-hidden="true">
    <path d="M20 2 V82 M6 64 L20 86 L34 64" stroke="var(--green)" stroke-width="4" fill="none"/>
  </svg>

  <div class="rule rule--one"></div>

  <div class="pitch pitch--finding">Are your customers<br><b>finding you</b> online ?</div>

  <div class="rule rule--two"></div>

  <div class="pitch pitch--more">
    <div class="more-intro">Do you need</div>
    <div class="more-word">More</div>
    <div class="more-customers">Customers</div>
    <div class="more-business">for your business ?</div>
  </div>

  <div class="rule rule--three"></div>
  <p class="tagline">Let us help you grow your business online</p>

  <svg class="front-wave" width="560" height="150" viewBox="0 0 560 150" aria-hidden="true">
    <path d="M0 40 Q140 0 300 45 T560 55 V150 H0 Z" fill="var(--blue)"/>
  </svg>
  <div class="logo-box logo-box--large">LOGO<span>HERE</span></div>
  <p class="front-call">Call <strong>0100 555 0192</strong> for a <strong>FREE</strong></p>
</section>

</body>
</html>
```